RESIDENTIAL CONSTRUCTION

We are a company that specializes in building custom residential homes, the design should also emphasize that quality and service is our priority.

Industry/Entity Type

Construction Company

Contact Information for Business Card

Contact Person: Marcus Lindqvist
Company Address: 273 West Alder Ave San Jose , Ca 95380
Phone Number : 408-731-2946
Email Address: Stoneridgehomes517@mailvista.net

Font styles to use
Sans Serif

Colors
ec1f27

Requirements
Must have
• CSLB # 7362015
Nice to have
• needs to have same color as logo i uploaded, we will be printing these on a clear plastic card.

```html
<!DOCTYPE html>
<html lang="en">
<head>
<meta charset="utf-8">
<title>Stoneridge Homes – Business Card</title>
<link rel="stylesheet" href="https://fonts.googleapis.com/css2?family=Oswald:wght@500;600&family=Open+Sans:wght@400;600&display=swap">
<style>
  :root {
    --brand-red: #ec1f27;
    --ink: #111111;
    --text-grey: #3a3a3a;
    --card-black: #161616;
    --card-white: #ffffff;
    --stage: #2a2a2a;
  }
  * { box-sizing: border-box; margin: 0; padding: 0; }
  html, body { width: 1200px; height: 716px; overflow: hidden; }
  body {
    background: var(--stage);
    position: relative;
    font-family: "Open Sans", Arial, sans-serif;
  }
  .card {
    position: absolute;
    top: 215px;
    width: 500px;
    height: 286px;
    border-radius: 18px;
    overflow: hidden;
  }
  .card--front { left: 70px; background: var(--card-black); }
  .card--back { left: 630px; background: var(--card-white); }

  .brand {
    display: flex;
    align-items: center;
    gap: 12px;
    font-family: "Oswald", Arial, sans-serif;
    font-weight: 600;
    color: var(--brand-red);
    text-transform: uppercase;
    letter-spacing: 1px;
    white-space: nowrap;
    line-height: 1;
  }
  .brand__square { width: 26px; height: 26px; background: var(--brand-red); flex: none; }
  .card--front .brand {
    position: absolute; left: 50%; top: 50%;
    transform: translate(-50%, -50%);
    font-size: 44px;
  }

  .holder { position: absolute; left: 28px; top: 26px; }
  .holder__name {
    font-family: "Oswald", Arial, sans-serif;
    font-weight: 600; font-size: 28px; color: var(--ink);
    text-transform: uppercase; letter-spacing: 0.5px; line-height: 1.1;
  }
  .holder__title {
    font-family: "Oswald", Arial, sans-serif;
    font-weight: 500; font-size: 15px; color: var(--brand-red);
    text-transform: uppercase; letter-spacing: 0.5px; margin-top: 2px;
  }
  .holder__rule { width: 52px; height: 2px; background: var(--brand-red); margin-top: 10px; }

  .contact-list {
    position: absolute; left: 28px; bottom: 28px;
    list-style: none; font-size: 13px; color: var(--text-grey);
  }
  .contact-list li { display: flex; align-items: center; gap: 9px; line-height: 21px; }
  .contact-list svg { width: 12px; height: 12px; fill: var(--brand-red); flex: none; }

  .card--back .brand {
    position: absolute; right: 28px; bottom: 22px;
    writing-mode: vertical-rl; transform: rotate(180deg);
    font-size: 24px;
    gap: 10px;
  }
  .card--back .brand__square { width: 20px; height: 20px; }
</style>
</head>
<body>
  <section class="card card--front" aria-label="Card front">
    <div class="brand"><span class="brand__square"></span>Stoneridge Homes</div>
  </section>

  <section class="card card--back" aria-label="Card back">
    <div class="holder">
      <h1 class="holder__name">Marcus Lindqvist</h1>
      <p class="holder__title">Job Title | CSLB # 7362015</p>
      <div class="holder__rule"></div>
    </div>

    <ul class="contact-list">
      <li>
        <svg viewBox="0 0 24 24" aria-hidden="true"><path d="M6.6 10.8a15.1 15.1 0 0 0 6.6 6.6l2.2-2.2c.3-.3.7-.4 1-.2 1.1.4 2.3.6 3.6.6.6 0 1 .4 1 1V20c0 .6-.4 1-1 1A17 17 0 0 1 3 4c0-.6.4-1 1-1h3.5c.6 0 1 .4 1 1 0 1.3.2 2.5.6 3.6.1.3 0 .7-.2 1z"/></svg>
        408-731-2946
      </li>
      <li>
        <svg viewBox="0 0 24 24" aria-hidden="true"><path d="M2 5h20v14H2zm2 2v.4l8 5 8-5V7z"/></svg>
        Stoneridgehomes517@mailvista.net
      </li>
      <li>
        <svg viewBox="0 0 24 24" aria-hidden="true"><path d="M12 2a7 7 0 0 0-7 7c0 5.2 7 13 7 13s7-7.8 7-13a7 7 0 0 0-7-7zm0 9.5A2.5 2.5 0 1 1 12 6.5a2.5 2.5 0 0 1 0 5z"/></svg>
        273 West Alder Ave San Jose , Ca 95380
      </li>
    </ul>

    <div class="brand"><span class="brand__square"></span>Stoneridge Homes</div>
  </section>
</body>
</html>
```